UI/ UX Design for ERP Software

We need a new UX/UI interface for a ERP software for property managers. Our CMMS / ERP solution is made based on responsive design technologies and is coded in PHP.
The overall UX to be similar to Tev Ulna - easy navigation, intuitive menus.

Industry/Entity Type

Property Management

Number of Pages Required

5+ page

Requirements
Must have
• Round dock buttons
Consistent icons across the application
Enough Spacing between buttons/icons/ menu
Consistent Font
Nice to have
• We would like the UX to allow the users to use the application without /minimum training.
Should not have
• we don't want anything that is classic with respect to UX

```html
<!DOCTYPE html>
<html lang="en">
<head>
<meta charset="utf-8">
<title>Domora — Active Dashboard</title>
<link href="https://fonts.googleapis.com/css2?family=Lato:wght@400;700&display=swap" rel="stylesheet">
<style>
:root{
  --bg:#f1f1f1;
  --white:#ffffff;
  --sidebar:#434e5a;
  --accent:#0a8fe6;
  --card-top:#0aaaf6;
  --card-bottom:#0a7de8;
  --link:#0d8fe0;
  --text:#333b44;
  --muted:#5d6670;
  --grid:#dcdcdc;
  --tab-idle:#c9cbcd;
  --bar:#1aa3e8;
}
*{box-sizing:border-box;margin:0;padding:0}
html,body{width:1200px;height:861px;overflow:hidden}
body{position:relative;background:var(--bg);font-family:'Lato',sans-serif;color:var(--text)}
.topbar{position:absolute;left:0;top:0;width:1200px;height:84px;background:var(--white)}
.brand{position:absolute;left:30px;top:26px;display:flex;align-items:center;gap:8px;font-size:26px;font-weight:700;color:var(--accent)}
.brand-mark{width:18px;height:18px;background:var(--accent);border-radius:3px}
.divider{position:absolute;left:210px;top:18px;width:1px;height:49px;background:#999}
.crumb{position:absolute;left:222px;top:33px;display:flex;align-items:center;gap:9px;font-size:12px;letter-spacing:.3px;color:var(--text)}
.user{position:absolute;left:1061px;top:27px;display:flex;align-items:center;gap:7px;font-size:11px;color:var(--text)}
.avatar{width:28px;height:28px;border:1.5px solid #666;border-radius:50%;display:flex;align-items:center;justify-content:center}
.sidebar{position:absolute;left:0;top:84px;width:50px;height:777px;background:var(--sidebar)}
.dock-item{height:32px;display:flex;align-items:center;justify-content:center}
.dock-item.active{height:43px;background:var(--accent)}
.dock-item svg{width:10px;height:10px;fill:#fff}
.stat{position:absolute;top:113px;width:207px;height:107px;background:linear-gradient(var(--card-top),var(--card-bottom));color:#fff;padding:0 14px}
.stat-label{position:absolute;left:14px;font-size:10px;font-weight:700;letter-spacing:.3px;line-height:1.15}
.stat-value{position:absolute;left:14px;top:68px;font-size:18px;font-weight:700;letter-spacing:.3px}
.stat svg{position:absolute;right:16px;top:34px;fill:#fff}
.tabs{position:absolute;left:69px;top:242px;display:flex;gap:5px}
.tab{width:144px;height:35px;background:var(--tab-idle);color:#fff;font-size:10.5px;display:flex;align-items:center;justify-content:center;gap:10px}
.tab.active{background:var(--white);color:#1566c0;font-weight:700}
.tab svg{width:10px;height:10px}
.panel{position:absolute;left:69px;top:277px;width:1113px;height:362px;background:var(--white)}
.range{position:absolute;left:87px;top:310px;display:flex;align-items:center;gap:14px;font-size:11px;font-weight:700;color:var(--muted)}
.chart{position:absolute;left:0;top:0}
.legend{position:absolute;left:85px;top:600px;display:flex;gap:10px;font-size:7.5px;color:var(--text)}
.legend span{display:flex;align-items:center;gap:4px}
.legend i{width:11px;height:11px;display:inline-block}
.box{position:absolute;top:656px;height:177px;background:var(--white);padding:0 15px}
.box-title{position:absolute;left:15px;top:673px;display:flex;align-items:center;gap:11px;font-size:15px;color:var(--text);letter-spacing:.2px}
.box h3{font-size:12px;font-weight:700;color:var(--link);letter-spacing:.2px;margin-top:0}
.box p{font-size:11px;color:var(--text);margin:3px 0 15px;letter-spacing:.2px}
.box .entries{position:absolute;left:15px;top:50px}
.view-all{position:absolute;left:15px;top:149px;font-size:10px;font-weight:700;color:var(--text);text-decoration:underline}
</style>
</head>
<body>
<header class="topbar">
  <div class="brand"><span class="brand-mark"></span>Domora</div>
  <div class="divider"></div>
  <div class="crumb">
    <svg width="14" height="12" viewBox="0 0 14 12"><path d="M7 0 0 6h2v6h4V8h2v4h4V6h2z" fill="#434e5a"/></svg>
    ACTIVE DASHBOARD
  </div>
  <div class="user">
    <span class="avatar"><svg width="12" height="13" viewBox="0 0 12 13"><circle cx="6" cy="3.5" r="3.2" fill="#222"/><path d="M0 13c0-4 3-5.5 6-5.5s6 1.5 6 5.5z" fill="#222"/></svg></span>
    USER NAME
    <svg width="9" height="6" viewBox="0 0 9 6" style="margin-left:10px"><path d="M1 1l3.5 3.5L8 1" stroke="#333" stroke-width="1.6" fill="none"/></svg>
  </div>
</header>

<nav class="sidebar">
  <div class="dock-item active"><svg viewBox="0 0 10 10"><path d="M5 1a5 5 0 0 0-5 5v2h10V6a5 5 0 0 0-5-5z"/></svg></div>
  <div class="dock-item"><svg viewBox="0 0 10 10"><circle cx="5" cy="3" r="2"/><circle cx="1.6" cy="4" r="1.4"/><circle cx="8.4" cy="4" r="1.4"/><path d="M1 9c0-3 8-3 8 0z"/></svg></div>
  <div class="dock-item"><svg viewBox="0 0 10 10"><path d="M5 0 0 5h1.5v5h7V5H10z"/></svg></div>
  <div class="dock-item"><svg viewBox="0 0 10 10"><circle cx="5" cy="5" r="5"/></svg></div>
  <div class="dock-item"><svg viewBox="0 0 10 10"><rect x="1.5" width="7" height="10"/></svg></div>
  <div class="dock-item"><svg viewBox="0 0 10 10"><circle cx="5" cy="3" r="2.5"/><path d="M0 10c0-5 10-5 10 0z"/></svg></div>
  <div class="dock-item"><svg viewBox="0 0 10 10"><circle cx="3" cy="3" r="2"/><circle cx="7.5" cy="3.5" r="1.6"/><path d="M0 9c0-4 10-4 10 0z"/></svg></div>
  <div class="dock-item"><svg viewBox="0 0 10 10"><rect x="1.5" width="7" height="10"/></svg></div>
  <div class="dock-item"><svg viewBox="0 0 10 10"><circle cx="3.5" cy="5" r="3"/><circle cx="8" cy="3" r="2"/></svg></div>
  <div class="dock-item"><svg viewBox="0 0 10 10"><rect x="1.5" width="7" height="10"/></svg></div>
  <div class="dock-item"><svg viewBox="0 0 10 10"><rect x="1.5" width="7" height="10"/></svg></div>
  <div class="dock-item"><svg viewBox="0 0 10 10"><circle cx="4" cy="4" r="3" fill="none" stroke="#fff" stroke-width="1.6"/><path d="M6 6l3.5 3.5" stroke="#fff" stroke-width="1.8"/></svg></div>
  <div class="dock-item"><svg viewBox="0 0 10 10"><path d="M0 0h1v9h9v1H0z"/><rect x="2" y="4" width="1.5" height="4"/><rect x="4.5" y="2" width="1.5" height="6"/><rect x="7" y="5" width="1.5" height="3"/></svg></div>
  <div class="dock-item"><svg viewBox="0 0 10 10"><circle cx="5" cy="5" r="5"/></svg></div>
  <div class="dock-item"><svg viewBox="0 0 10 10"><rect y="1" width="10" height="2"/><rect y="4" width="10" height="2"/><rect y="7" width="10" height="2"/></svg></div>
  <div class="dock-item"><svg viewBox="0 0 10 10"><rect y="2" width="10" height="6"/></svg></div>
  <div class="dock-item"><svg viewBox="0 0 10 10"><ellipse cx="4" cy="4" rx="4" ry="3"/><ellipse cx="6.5" cy="6.5" rx="3.5" ry="2.5"/></svg></div>
  <div class="dock-item"><svg viewBox="0 0 10 10"><path d="M5 5V0a5 5 0 1 0 5 5z"/></svg></div>
  <div class="dock-item"><svg viewBox="0 0 10 10"><path d="M0 0h1v9h9v1H0zM2 8l2-4 2 2 3-4v6z"/></svg></div>
  <div class="dock-item"><svg viewBox="0 0 10 10"><rect x="2" width="7" height="8"/><rect x="0.5" y="2" width="7" height="8"/></svg></div>
  <div class="dock-item"><svg viewBox="0 0 10 10"><rect x="2" width="7" height="8"/><rect x="0.5" y="2" width="7" height="8"/></svg></div>
  <div class="dock-item"><svg viewBox="0 0 10 10"><circle cx="5" cy="5" r="4.5"/></svg></div>
  <div class="dock-item"><svg viewBox="0 0 10 10"><path d="M9 1 5 5 1 9l1 1 4-4 4-4z"/></svg></div>
</nav>

<section class="stat" style="left:69px">
  <div class="stat-label" style="top:78px;top:79px;transform:translateY(-46px)">PROPERTIES</div>
  <div class="stat-value" style="left:16px">3</div>
  <svg width="48" height="40" viewBox="0 0 48 40" style="top:33px"><path d="M24 2 1 22l4 4 3-2.6V40h12V28h8v12h12V23.4l3 2.6 4-4z"/></svg>
</section>
<section class="stat" style="left:296px">
  <div class="stat-label" style="top:29px">TENANTS</div>
  <div class="stat-value">8</div>
  <svg width="42" height="30" viewBox="0 0 42 30" style="top:40px"><circle cx="21" cy="7" r="7"/><circle cx="7" cy="10" r="5"/><circle cx="35" cy="10" r="5"/><path d="M8 30c0-11 26-11 26 0zM0 25c0-7 10-8 11-5-2 1-4 3-4 5zM42 25c0-7-10-8-11-5 2 1 4 3 4 5z"/></svg>
</section>
<section class="stat" style="left:522px">
  <div class="stat-label" style="top:43px">TOTAL PROPERTIES<br>AREA</div>
  <div class="stat-value">422,000.00 sq.ft.</div>
  <svg width="28" height="28" viewBox="0 0 28 28" style="top:40px"><path d="M0 0h10L7 3l5 5-4 4-5-5-3 3zM28 0v10l-3-3-5 5-4-4 5-5-3-3zM0 28V18l3 3 5-5 4 4-5 5 3 3zM28 28H18l3-3-5-5 4-4 5 5 3-3z"/></svg>
</section>
<section class="stat" style="left:749px">
  <div class="stat-label" style="top:49px">RENTED AREA</div>
  <div class="stat-value">233,500.00 sq.ft</div>
  <svg width="28" height="28" viewBox="0 0 28 28" style="top:40px"><path d="M0 0h10L7 3l5 5-4 4-5-5-3 3zM28 0v10l-3-3-5 5-4-4 5-5-3-3zM0 28V18l3 3 5-5 4 4-5 5 3 3zM28 28H18l3-3-5-5 4-4 5 5 3-3z"/></svg>
</section>
<section class="stat" style="left:975px">
  <div class="stat-label" style="top:49px">VACANCIES AREA</div>
  <div class="stat-value">188,500.00 sq.ft</div>
  <svg width="28" height="28" viewBox="0 0 28 28" style="top:40px"><path d="M0 0h10L7 3l5 5-4 4-5-5-3 3zM28 0v10l-3-3-5 5-4-4 5-5-3-3zM0 28V18l3 3 5-5 4 4-5 5 3 3zM28 28H18l3-3-5-5 4-4 5 5 3-3z"/></svg>
</section>

<div class="tabs">
  <div class="tab active"><svg viewBox="0 0 10 10"><circle cx="5" cy="5" r="4.2" fill="none" stroke="currentColor" stroke-width="1.2"/><path d="M5 2.5V5h2" stroke="currentColor" fill="none"/></svg>LAST 7 DAYS</div>
  <div class="tab"><svg viewBox="0 0 10 10"><circle cx="5" cy="5" r="4.2" fill="none" stroke="currentColor" stroke-width="1.2"/><path d="M5 2.5V5h2" stroke="currentColor" fill="none"/></svg>LAST MONTHS</div>
  <div class="tab"><svg viewBox="0 0 10 10"><circle cx="5" cy="5" r="4.2" fill="none" stroke="currentColor" stroke-width="1.2"/><path d="M5 2.5V5h2" stroke="currentColor" fill="none"/></svg>LAST 3 MONTHS</div>
  <div class="tab"><svg viewBox="0 0 10 10"><circle cx="5" cy="5" r="4.2" fill="none" stroke="currentColor" stroke-width="1.2"/><path d="M5 2.5V5h2" stroke="currentColor" fill="none"/></svg>NEXT 7 DAYS</div>
  <div class="tab"><svg viewBox="0 0 10 10"><circle cx="5" cy="5" r="4.2" fill="none" stroke="currentColor" stroke-width="1.2"/><path d="M5 2.5V5h2" stroke="currentColor" fill="none"/></svg>NEXT MONTHS</div>
  <div class="tab"><svg viewBox="0 0 10 10"><circle cx="5" cy="5" r="4.2" fill="none" stroke="currentColor" stroke-width="1.2"/><path d="M5 2.5V5h2" stroke="currentColor" fill="none"/></svg>NEXT 3 MONTHS</div>
</div>

<div class="panel"></div>
<div class="range">
  <svg width="13" height="11" viewBox="0 0 13 11"><rect x="0" y="9" width="2" height="2" fill="#555"/><rect x="3" y="7" width="2" height="4" fill="#555"/><rect x="6" y="4" width="2" height="7" fill="#555"/><rect x="9" y="0" width="2" height="11" fill="#555"/></svg>
  12/27/2020 - 01/03/2021
</div>

<svg class="chart" width="1200" height="600" viewBox="0 0 1200 600" font-family="Lato, sans-serif">
  <g fill="#444"><rect x="86" y="352" width="11" height="1.4"/><rect x="86" y="355.5" width="11" height="1.4"/><rect x="86" y="359" width="11" height="1.4"/></g>
  <g stroke="var(--grid)" stroke-width="0.8">
    <line x1="141" y1="356" x2="1155" y2="356"/><line x1="141" y1="394" x2="1155" y2="394"/>
    <line x1="141" y1="432" x2="1155" y2="432"/><line x1="141" y1="469" x2="1155" y2="469"/>
    <line x1="141" y1="507" x2="1155" y2="507"/>
  </g>
  <g stroke="#c4c4c4" stroke-width="0.8">
    <line x1="141" y1="545" x2="1155" y2="545"/>
    <line x1="141" y1="545" x2="141" y2="563"/><line x1="268" y1="545" x2="268" y2="563"/>
    <line x1="394" y1="545" x2="394" y2="563"/><line x1="521" y1="545" x2="521" y2="563"/>
    <line x1="648" y1="545" x2="648" y2="563"/><line x1="775" y1="545" x2="775" y2="563"/>
    <line x1="901" y1="545" x2="901" y2="563"/><line x1="1028" y1="545" x2="1028" y2="563"/>
    <line x1="1155" y1="545" x2="1155" y2="563"/>
  </g>
  <g font-size="10.5" fill="#444" text-anchor="end">
    <text x="131" y="360">1.25</text><text x="131" y="397">1</text><text x="131" y="436">0.75</text>
    <text x="131" y="473">0.5</text><text x="131" y="510">0.25</text><text x="131" y="548">0</text>
  </g>
  <g font-size="9" fill="#555" text-anchor="middle">
    <text x="204" y="562">12/27/2020</text><text x="331" y="562">12/28/2020</text>
    <text x="457" y="562">12/29/2020</text><text x="584" y="562">12/30/2020</text>
    <text x="711" y="562">12/31/2020</text><text x="838" y="562">01/01/2021</text>
    <text x="964" y="562">01/03/2021</text><text x="1091" y="562">01/02/2021</text>
  </g>
  <rect x="493" y="356" width="9" height="189" fill="var(--bar)"/>
</svg>

<div class="legend">
  <span><i style="background:#1aa3e8"></i>SCHEDULED MAINTENANCE</span>
  <span><i style="background:#3a9a1a"></i>COMPLETED SCHEDULED MAINTENANCE</span>
  <span><i style="background:#f57a0c"></i>FUTURE SCHEDULED MAINTENANCE</span>
  <span><i style="background:#444"></i>SCHEDULED WORK ORDERS</span>
  <span><i style="background:#9b6ae0"></i>COMPLETED WORK ORDERS</span>
  <span><i style="background:#ee3a5a"></i>PROPERTY INSPECTIONS</span>
  <span><i style="background:#f7b500"></i>COMPLETED PROPERTY INSPECTIONS</span>
</div>

<section class="box" style="left:69px;width:356px">
  <div class="box-title" style="top:17px"><svg width="11" height="14" viewBox="0 0 11 14"><path d="M0 0h7l4 4v10H0z" fill="#1566c0"/></svg>WORK ORDERS</div>
  <div class="entries">
    <h3>SED UT PERSPICIATIS UNDE OMNIS ISTE</h3>
    <p>Nemo enim ipsam voluptatem quia voluptas sit aspernatur</p>
    <h3>SED UT PERSPICIATIS UNDE OMNIS ISTE</h3>
    <p>Nemo enim ipsam voluptatem quia voluptas sit aspernatur</p>
  </div>
  <a class="view-all">VIEW ALL &nbsp;&gt;&gt;</a>
</section>
<section class="box" style="left:445px;width:357px">
  <div class="box-title" style="top:17px"><svg width="11" height="14" viewBox="0 0 11 14"><path d="M0 0h7l4 4v10H0z" fill="#1566c0"/></svg>PURCHASE ORDERS</div>
  <div class="entries">
    <h3>SED UT PERSPICIATIS UNDE OMNIS ISTE</h3>
    <p>Nemo enim ipsam voluptatem quia voluptas sit aspernatur</p>
    <h3>SED UT PERSPICIATIS UNDE OMNIS ISTE</h3>
    <p>Nemo enim ipsam voluptatem quia voluptas sit aspernatur</p>
  </div>
  <a class="view-all">VIEW ALL &nbsp;&gt;&gt;</a>
</section>
<section class="box" style="left:825px;width:357px">
  <div class="box-title" style="top:17px"><svg width="14" height="14" viewBox="0 0 14 14"><circle cx="5.5" cy="5.5" r="4.3" fill="none" stroke="#1566c0" stroke-width="2"/><path d="M8.8 8.8 13 13" stroke="#1566c0" stroke-width="2.4"/></svg>PROPERTY INSPECTION</div>
  <div class="entries">
    <h3>SED UT PERSPICIATIS UNDE OMNIS ISTE</h3>
    <p>Nemo enim ipsam voluptatem quia voluptas sit aspernatur</p>
    <h3>SED UT PERSPICIATIS UNDE OMNIS ISTE</h3>
    <p>Nemo enim ipsam voluptatem quia voluptas sit aspernatur</p>
  </div>
  <a class="view-all">VIEW ALL &nbsp;&gt;&gt;</a>
</section>
</body>
</html>
```